Bright and beautiful business card for a coach

I'm a personal and business coach based in Perth, Australia. I need a business card that whilst subtle and elegant, will stand out and appeal on a table full of cards.

My business name is Fern Mentoring and the business card must represent the warmth and brightness implied in the name, without being gimmicky. It must have a warmth and appeal and be easy to read.

I prefer clean, minimalist designs.

It must align with the feel of my website and socials: https://www.fernmentoring-example.com.au/
https://www.instagram.com/fernmentoringau/
https://www.facebook.com/fernmentoringau
Updates

Hi Designers Thank you so much for taking the time to submit designs. I wonder if I could have explained myself a little better. Most of the designs that have been submitted look rather formal and many have quite corporate looking embellishments on them (to my eye). I would like softer, warmer, more organic. I’m open to people playing about and being more abstract, using softer embellishments (e.g the line drawing flowers and grasses I’ve used in my socials) incorporating other colours from my palette or like the social icons in my email signature (in PDF), perhaps playing with size/oversize, playing with the bleed. Please don’t be constrained by what I’ve already done, it merely needs to compliment. I’m sorry if I’m not using the right words or have led you astray. I’m no designer, but I’ve done my website, socials, email signature etc all myself (my logo was a design contest) and I was really hoping for my business card to be something more creative than I could have made with a template. Reminder: No black cards/sides please. Thank you 😊

Target Market(s)

Individuals, most likely but not all female. Creative thinkers. Likely professionals.

Industry/Entity Type

Business & Personal Coach

Contact Information for Business Card

(Fern Mentoring Logo) Name: Greta Pellham; Title: Business & Personal Coach; Phone number: +61 (0)458 913307; Email: greta@fernmentoring-example.com.au; Website: https://fernmentoring-example.com.au; Social icons for Facebook, Instagram & LinkedIn: @fernmentoringAU. Optional strapline: "A thinking partner to help you cut through the noise"

Font styles to use
Sans Serif

Colors
00AB8E
00BBA5
67D7C9
C6EFE9
E9F9F6
59FF00
82FF00
B8FF75
E3FFCB
F4FFEA
FFC000
F8CF3A
FAE287
FDF2CF
FEFAEE

Requirements
Must have
• Must align with feel of my website and socials. Must have a pop of #FFC000 (possibly whole of one side, or at least a block). Bright or white background. Easy to read.
Nice to have
• Possibly incorporate the sunshine/grass picture I have used in website and socials - will upload.
Should not have
• Must not be black or dark. Not impersonal or corporate looking.

```html
<!DOCTYPE html>
<html lang="en">
<head>
<meta charset="utf-8">
<title>Fern Mentoring – Business Card</title>
<link rel="stylesheet" href="https://fonts.googleapis.com/css2?family=Poppins:wght@400;500&family=Mrs+Saint+Delafield&display=swap">
<style>
  :root {
    --page-bg: #dcdee0;
    --card-bg: #ffffff;
    --gold-deep: #c47f2b;
    --gold: #d48c1f;
    --sun: #ffc000;
    --ink-grey: #8a8a8a;
    --logo-grey: #9a9a9a;
    --white: #ffffff;
  }
  * { box-sizing: border-box; margin: 0; padding: 0; }
  html, body {
    width: 1200px; height: 928px; overflow: hidden;
    background: var(--page-bg);
    font-family: "Poppins", sans-serif;
  }
  .canvas { position: relative; width: 1200px; height: 928px; }

  .card {
    position: absolute; left: 264px; width: 672px; height: 384px;
    background: var(--card-bg); border-radius: 18px; overflow: hidden;
  }
  .card--front { top: 58px; }
  .card--back  { top: 484px; }

  /* brand mark */
  .brand {
    position: absolute; display: flex; align-items: center; gap: 14px;
    color: var(--gold); font-weight: 500; white-space: nowrap;
  }
  .brand__dot { border-radius: 50%; background: var(--sun); flex: none; }
  .card--front .brand { left: 0; right: 0; top: 158px; justify-content: center; font-size: 46px; }
  .card--front .brand__dot { width: 30px; height: 30px; }
  .card--back .brand { left: 352px; top: 70px; font-size: 30px; gap: 10px; }
  .card--back .brand__dot { width: 20px; height: 20px; }

  .strapline {
    position: absolute; left: 0; right: 0; top: 322px; height: 32px;
    background: linear-gradient(90deg, var(--gold-deep) 0%, #e0a020 60%, var(--sun) 100%);
    color: var(--white); font-weight: 500; font-size: 17.5px; letter-spacing: 0.6px;
    display: flex; align-items: center; justify-content: center;
  }

  /* back side */
  .person { position: absolute; left: 37px; top: 140px; }
  .person__name {
    font-family: "Mrs Saint Delafield", cursive;
    font-size: 66px; line-height: 1; color: var(--gold);
  }
  .person__title { margin-top: 6px; font-size: 15.5px; color: var(--ink-grey); }

  .contact {
    position: absolute; left: 372px; top: 241px;
    list-style: none; font-size: 14.5px; line-height: 23.5px;
    color: var(--ink-grey); letter-spacing: 0.3px;
  }
  .social {
    position: absolute; left: 373px; top: 325px;
    display: flex; align-items: center; gap: 7px;
    font-size: 14.5px; color: var(--ink-grey);
  }
  .social__badge {
    width: 25px; height: 25px; border-radius: 50%;
    background: linear-gradient(135deg, var(--gold-deep), var(--sun));
  }
  .social__handle { margin-left: 2px; }
</style>
</head>
<body>
<main class="canvas">

  <section class="card card--front" aria-label="Card front">
    <div class="brand"><span class="brand__dot"></span>Fern Mentoring</div>
    <p class="strapline">A thinking partner to help you cut through the noise</p>
  </section>

  <section class="card card--back" aria-label="Card back">
    <div class="brand"><span class="brand__dot"></span>Fern Mentoring</div>

    <div class="person">
      <p class="person__name">Greta Pellham</p>
      <p class="person__title">Business &amp; Personal Coach</p>
    </div>

    <ul class="contact">
      <li>+61 (0)458 913307</li>
      <li>greta@fernmentoring-example.com.au</li>
      <li>www.fernmentoring-example.com.au</li>
    </ul>

    <div class="social">
      <span class="social__badge" aria-hidden="true"></span>
      <span class="social__badge" aria-hidden="true"></span>
      <span class="social__badge" aria-hidden="true"></span>
      <span class="social__handle">@fernmentoringAU</span>
    </div>
  </section>

</main>
</body>
</html>
```